Baby Boutique Needs a Business Card Design

We need a modern double sided business card design using the attached logo for Little Wren Nook.

Little Wren Nook is a baby boutique which sells only handmade clothing and accessories for both boys and girls. Our store will live exclusively online.

We would like to only use the colors that have been used in the logo.

Target Market(s)

Potential wholesale clients, Small business owners

Industry/Entity Type

Retail

Contact Information for Business Card

Name Gideon R. Falkner (Owner)
Email sales@littlewrennook.example
Main Phone 555-203-7719
Cell phone 555-203-7746
Website www.LittleWrenNook.example

Font styles to use
Sans Serif

Colors

Designer to choose colors to be used in the design.

Requirements
Must have
• -Would like to have icons that indentify the contact information.
• -Include our website
• -Include our tagline in a small area near the bottom. "Handmade Baby Creations"
• -Would like to include Facebook and Instagram Icons
• -
Nice to have
• Would like to have a simple back side with the logo.
• Something along the lines of the meadowfield lending card attached.

```html
<!DOCTYPE html>
<html lang="en">
<head>
<meta charset="utf-8">
<title>Little Wren Nook — Business Card</title>
<link rel="stylesheet" href="https://fonts.googleapis.com/css2?family=Oswald:wght@500&family=Work+Sans:wght@400;500&display=swap">
<style>
  :root {
    --backdrop: #262626;
    --card: #1c1c1c;
    --coral: #e35d5b;
    --mint: #72d3c0;
    --ink: #f2f2f2;
    --card-w: 660px;
    --card-h: 377px;
  }
  * { box-sizing: border-box; margin: 0; padding: 0; }
  html, body {
    width: 1200px; height: 900px; overflow: hidden;
    background: var(--backdrop);
    font-family: "Work Sans", sans-serif;
  }
  .card {
    position: absolute;
    left: 270px;
    width: var(--card-w);
    height: var(--card-h);
    background: var(--card);
    border-bottom: 7px solid var(--coral);
    box-shadow: 0 10px 24px rgba(0,0,0,.45);
  }
  .card--front { top: 48px; }
  .card--back  { top: 475px; }

  /* Front */
  .brand {
    position: absolute;
    left: 0; right: 0; top: 130px;
    display: flex; align-items: center; justify-content: center; gap: 14px;
  }
  .brand__dot {
    width: 16px; height: 16px; border-radius: 50%;
    background: var(--coral);
  }
  .brand__name {
    font-family: "Work Sans", sans-serif;
    font-weight: 500;
    font-size: 44px;
    color: var(--mint);
    letter-spacing: .5px;
  }

  /* Back */
  .owner {
    position: absolute;
    right: 392px; top: 140px;
    text-align: right;
  }
  .owner__name {
    font-family: "Oswald", sans-serif;
    font-weight: 500;
    font-size: 31px;
    line-height: 1.1;
    color: var(--coral);
    letter-spacing: 1px;
    text-transform: uppercase;
    white-space: nowrap;
  }
  .owner__role {
    font-size: 16px;
    color: var(--ink);
    letter-spacing: .5px;
  }
  .divider {
    position: absolute;
    left: 290px; top: 138px;
    width: 2px; height: 80px;
    background: var(--mint);
  }
  .contact {
    position: absolute;
    left: 312px; top: 138px;
    list-style: none;
  }
  .contact__item {
    display: flex; align-items: center; gap: 10px;
    height: 21px;
    font-size: 16px;
    color: var(--ink);
    letter-spacing: .6px;
  }
  .contact__icon { width: 11px; height: 11px; flex: none; }
  .footer {
    position: absolute;
    left: 210px; top: 305px;
    display: flex; align-items: center; gap: 12px;
  }
  .social { width: 20px; height: 20px; background: var(--coral); border-radius: 3px; }
  .tagline {
    margin-left: 14px;
    font-size: 17px;
    color: var(--ink);
    letter-spacing: 1px;
  }
</style>
</head>
<body>

<section class="card card--front">
  <div class="brand">
    <span class="brand__dot"></span>
    <span class="brand__name">Little Wren Nook</span>
  </div>
</section>

<section class="card card--back">
  <div class="owner">
    <p class="owner__name">Gideon R. Falkner</p>
    <p class="owner__role">Owner</p>
  </div>

  <div class="divider"></div>

  <ul class="contact">
    <li class="contact__item">
      <svg class="contact__icon" viewBox="0 0 12 12" fill="none" stroke="#e35d5b" stroke-width="1.4" stroke-linecap="round">
        <path d="M3 1.5l1.6 2.2-1 1.1a6 6 0 0 0 2.6 2.6l1.1-1 2.2 1.6-.8 1.6C5.5 9.7 2.3 6.5 1.4 2.3z"/>
      </svg>
      555-203-7719
    </li>
    <li class="contact__item">
      <svg class="contact__icon" viewBox="0 0 12 12" fill="none" stroke="#e35d5b" stroke-width="1.4">
        <rect x="3" y="1" width="6" height="10" rx="1"/>
        <line x1="5.2" y1="9" x2="6.8" y2="9"/>
      </svg>
      555-203-7746
    </li>
    <li class="contact__item">
      <svg class="contact__icon" viewBox="0 0 12 12" fill="none" stroke="#e35d5b" stroke-width="1.3">
        <rect x="1" y="2.5" width="10" height="7" rx=".8"/>
        <path d="M1.2 3l4.8 3.6L10.8 3"/>
      </svg>
      sales@littlewrennook.example
    </li>
    <li class="contact__item">
      <svg class="contact__icon" viewBox="0 0 12 12" fill="none" stroke="#e35d5b" stroke-width="1.2">
        <circle cx="6" cy="6" r="5"/>
        <ellipse cx="6" cy="6" rx="2.2" ry="5"/>
        <line x1="1" y1="6" x2="11" y2="6"/>
      </svg>
      www.LittleWrenNook.example
    </li>
  </ul>

  <div class="footer">
    <span class="social" aria-label="Social profile"></span>
    <span class="social" aria-label="Social profile"></span>
    <span class="tagline">Handmade Baby Creations</span>
  </div>
</section>

</body>
</html>
```